RTavenor Business Cards & Letterhead

I have a logo but need a design for some new business cards. We are a Design-Build Firm that specializes in the design and construction of commercial projects.
the cards need to be professional. no cartoon stuff.
i would like to have the cards in AI format so I can update the card as needed. Logo is provided.
Our Address is: 4187 Marlowe Ct. Brenton, Vermont 27614

```html
<!DOCTYPE html>
<html lang="en">
<head>
<meta charset="utf-8">
<title>RTavenor Business Card</title>
<link href="https://fonts.googleapis.com/css2?family=Open+Sans:wght@400;600;700;800&display=swap" rel="stylesheet">
<style>
  :root {
    --stage: #333333;
    --card: #1f1f23;
    --card-deep: #141416;
    --brand-blue: #1d7fd0;
    --brand-blue-dark: #0f5da3;
    --logo-grey: #7d7e82;
    --text-light: #f2f2f2;
    --panel-tone: #27313c;
  }
  * { margin: 0; padding: 0; box-sizing: border-box; }
  html, body {
    width: 1200px; height: 780px; overflow: hidden;
    background: var(--stage);
    font-family: "Open Sans", Arial, sans-serif;
  }
  .stage {
    width: 1200px; height: 780px;
    display: flex; align-items: center; justify-content: center; gap: 40px;
  }
  .card {
    position: relative;
    width: 540px; height: 309px;
    background: var(--card);
    overflow: hidden;
    box-shadow: 0 12px 30px rgba(0,0,0,0.45);
  }

  /* Back side */
  .card-back { background: var(--card-deep); }
  .back-texture {
    position: absolute; inset: 0;
    background: linear-gradient(200deg, #5a5a5e 0%, #2a2a2e 28%, #0d0d0f 55%, #060607 100%);
  }
  .back-brand {
    position: absolute; left: 50%; top: 50%;
    transform: translate(-50%, -50%);
    display: flex; align-items: center; gap: 12px;
  }

  /* Brand lockup */
  .brand-square {
    width: 26px; height: 26px; background: var(--brand-blue);
  }
  .brand-name {
    font-weight: 800; font-size: 36px; letter-spacing: 1px;
    color: var(--logo-grey); line-height: 1;
  }

  /* Front side */
  .front-brand {
    position: absolute; left: 30px; top: 36px;
    display: flex; align-items: center; gap: 12px;
  }
  .front-panel {
    position: absolute; left: 305px; top: 22px;
    width: 210px; height: 265px; border-radius: 18px 60px 60px 18px;
    background: linear-gradient(160deg, var(--panel-tone) 0%, #222a33 60%, #1f242b 100%);
    opacity: 0.85;
  }
  .name-band {
    position: absolute; right: 14px; top: 118px;
    width: 20px; height: 44px;
    background: linear-gradient(180deg, var(--brand-blue), var(--brand-blue-dark));
  }
  .holder {
    position: absolute; right: 40px; top: 116px; text-align: right;
  }
  .holder-name {
    font-weight: 700; font-size: 24px; color: var(--brand-blue);
    letter-spacing: 1px; line-height: 1.1;
  }
  .holder-title {
    font-weight: 600; font-size: 15px; color: var(--text-light);
    margin-top: 4px;
  }
  .address {
    position: absolute; left: 34px; top: 140px;
    font-size: 14px; line-height: 1.35; color: var(--text-light);
  }
  .contacts {
    position: absolute; left: 34px; bottom: 26px;
    list-style: none; font-size: 14px; line-height: 1.45; color: var(--text-light);
  }
  .contacts li { display: flex; align-items: center; gap: 8px; }
  .contacts svg { width: 13px; height: 13px; fill: var(--brand-blue); flex: none; }
</style>
</head>
<body>
<main class="stage">

  <section class="card card-back">
    <div class="back-texture" role="img" aria-label="Repeating monogram pattern fading from silver to black"></div>
    <div class="back-brand">
      <span class="brand-square"></span>
      <span class="brand-name">RTAVENOR</span>
    </div>
  </section>

  <section class="card card-front">
    <div class="front-panel" role="img" aria-label="Large faint brand monogram"></div>
    <div class="front-brand">
      <span class="brand-square"></span>
      <span class="brand-name">RTAVENOR</span>
    </div>

    <div class="name-band"></div>
    <div class="holder">
      <p class="holder-name">MARCUS TAVENOR</p>
      <p class="holder-title">Founder/President</p>
    </div>

    <p class="address">4187 Marlowe Ct. Brenton,<br>Vermont 27614</p>

    <ul class="contacts">
      <li>
        <svg viewBox="0 0 24 24" aria-hidden="true"><path d="M6.6 10.8a15.1 15.1 0 0 0 6.6 6.6l2.2-2.2a1 1 0 0 1 1-.25 11.4 11.4 0 0 0 3.6.57 1 1 0 0 1 1 1V20a1 1 0 0 1-1 1A17 17 0 0 1 3 4a1 1 0 0 1 1-1h3.5a1 1 0 0 1 1 1c0 1.25.2 2.45.57 3.57a1 1 0 0 1-.25 1z"/></svg>
        (555) 301-0148
      </li>
      <li>
        <svg viewBox="0 0 24 24" aria-hidden="true"><circle cx="12" cy="12" r="10"/></svg>
        www.rtavenor.com
      </li>
      <li>
        <svg viewBox="0 0 24 24" aria-hidden="true"><path d="M2 5h20v14H2z M2 5l10 8 10-8" /></svg>
        MT@RTavenor.com
      </li>
    </ul>
  </section>

</main>
</body>
</html>
```